Redesign of business card for Cedar Ridge Mechanical

We are looking for a new design for our business cards for Cedar Ridge Mechanical. We are a plumbing & HVAC construction company, operating on the West Coast of Canada and USA. Logo attached.
Industry/Entity Type
Construction - Plumbing & HVAC
Contact Information for Business Card
Name, address, phone numbers, email, website address
Look and feel
Each slider illustrates characteristics of the customer's brand and the style your logo design should communicate.

```html
<!DOCTYPE html>
<html lang="en">
<head>
<meta charset="utf-8">
<title>Cedar Ridge Mechanical – Business Card</title>
<link rel="stylesheet" href="https://fonts.googleapis.com/css2?family=Oswald:wght@500&family=Montserrat:wght@400;600&display=swap">
<style>
  :root {
    --backdrop: #7a6245;
    --card: #262626;
    --ink-light: #ffffff;
    --ink-soft: #e6e6e6;
    --ink-mark: #0e0e0e;
    --shadow: rgba(0, 0, 0, 0.45);
  }
  * { margin: 0; padding: 0; box-sizing: border-box; }
  html, body {
    width: 900px;
    height: 1200px;
    overflow: hidden;
    background: var(--backdrop);
  }
  .canvas { position: relative; width: 900px; height: 1200px; }

  .card {
    position: absolute;
    background: var(--card);
    border-radius: 24px;
    box-shadow: 0 10px 22px var(--shadow);
  }
  .card--front { left: 80px; top: 131px; width: 742px; height: 441px; }
  .card--back  { left: 78px; top: 638px; width: 744px; height: 440px; }

  .company-title {
    position: absolute;
    left: 36px; top: 46px;
    font-family: "Oswald", sans-serif;
    font-weight: 500;
    font-size: 33px;
    letter-spacing: 1.2px;
    color: var(--ink-light);
    text-transform: uppercase;
    line-height: 1;
  }
  .person {
    position: absolute;
    right: 56px; top: 36px;
    text-align: right;
    font-family: "Montserrat", sans-serif;
    color: var(--ink-light);
  }
  .person__name { font-weight: 600; font-size: 25px; line-height: 1.2; }
  .person__role { font-weight: 400; font-size: 15px; color: var(--ink-soft); margin-top: 2px; }

  .address {
    position: absolute;
    left: 34px; top: 243px;
    font-family: "Montserrat", sans-serif;
    font-size: 16px;
    line-height: 20px;
    color: var(--ink-soft);
  }
  .contact-list {
    position: absolute;
    left: 33px; top: 322px;
    list-style: none;
    font-family: "Montserrat", sans-serif;
    font-size: 16px;
    color: var(--ink-soft);
  }
  .contact-list li {
    display: flex;
    align-items: center;
    gap: 9px;
    height: 30.5px;
  }
  .contact-list svg { width: 16px; height: 16px; fill: var(--ink-light); flex: none; }

  .brand-mark {
    position: absolute;
    display: flex;
    align-items: center;
    font-family: "Oswald", sans-serif;
    font-weight: 500;
    color: var(--ink-mark);
    text-transform: uppercase;
    white-space: nowrap;
  }
  .brand-mark__square { background: var(--ink-mark); flex: none; }
  .brand-mark--front { right: 46px; top: 352px; font-size: 26px; gap: 12px; }
  .brand-mark--front .brand-mark__square { width: 34px; height: 34px; }
  .brand-mark--back {
    left: 0; right: 0; top: 190px;
    justify-content: center;
    font-size: 46px; gap: 18px; letter-spacing: 0.5px;
  }
  .brand-mark--back .brand-mark__square { width: 56px; height: 56px; }
</style>
</head>
<body>
<main class="canvas">
  <section class="card card--front">
    <h1 class="company-title">Cedar Ridge Mechanical</h1>
    <div class="person">
      <p class="person__name">Daniel Hart</p>
      <p class="person__role">Managing Director</p>
    </div>
    <p class="address">482 Harbor Crest Road<br>Fairview, MS 39120</p>
    <ul class="contact-list">
      <li>
        <svg viewBox="0 0 24 24" aria-hidden="true"><path d="M6.6 10.8a15.2 15.2 0 0 0 6.6 6.6l2.2-2.2a1 1 0 0 1 1-.25 11.4 11.4 0 0 0 3.6.57 1 1 0 0 1 1 1V20a1 1 0 0 1-1 1A17 17 0 0 1 3 4a1 1 0 0 1 1-1h3.5a1 1 0 0 1 1 1c0 1.25.2 2.45.57 3.57a1 1 0 0 1-.25 1z"/></svg>
        <span>555.302.4417</span>
      </li>
      <li>
        <svg viewBox="0 0 24 24" aria-hidden="true"><path d="M3 6h18v1.2l-9 5.6-9-5.6zM3 9.4l9 5.6 9-5.6V18H3z"/></svg>
        <span>info@cedarridgemechanical.com</span>
      </li>
      <li>
        <svg viewBox="0 0 24 24" aria-hidden="true"><path d="M12 2a10 10 0 1 0 0 20 10 10 0 0 0 0-20zm-1 17.9A8 8 0 0 1 4.2 10.5L9 15.3v1a2 2 0 0 0 2 2zm6.9-2.5A2 2 0 0 0 16 16h-1v-3a1 1 0 0 0-1-1H8v-2h2a1 1 0 0 0 1-1V7h2a2 2 0 0 0 2-2v-.4a8 8 0 0 1 2.9 12.8z"/></svg>
        <span>www.cedarridgemechanical.com</span>
      </li>
    </ul>
    <div class="brand-mark brand-mark--front">
      <span class="brand-mark__square"></span>
      <span>Cedar Ridge Mechanical</span>
    </div>
  </section>

  <section class="card card--back">
    <div class="brand-mark brand-mark--back">
      <span class="brand-mark__square"></span>
      <span>Cedar Ridge Mechanical</span>
    </div>
  </section>
</main>
</body>
</html>
```